Expanding National Maid Service Needs Redesign!

We need a redesigned home page for our residential cleaning company. Winner will be recognized as the designer for a brand about to go national within the United States. Winner will also become the first choice to continue working with the company to design at least 15 more pages.

Looking for redesign of homepage and redesign of logo (logo will use the same elements -- just organized differently with horizontal text).

For the design we are looking for a mix between the following websites:
www. tidyfleetcrew .example
This is our parent site that will be redesigned

www. sweeplancers .example
We really like the top/header having the three steps.
We would like to have the same font (proxima nova) and colors. We like the location and size of the booking form.
Love the section topics and would like to mimic that.

www. brightnookhelpers .example
We really like the clean art and use of colors.
We love the use of b-roll and branded images. Will provide for our website.

The perfect site would have the cleanliness, layout and booking form of Sweep Lancers and the excellent placement and use of branded images and b-roll of Bright Nook Helpers.

Link to branded images and b-roll is attached to the brief in a text file.

Please message me any questions. Good luck to everyone in the project!

Target Market(s)

Male and Female working professionals between the ages of 30-60 years old.

Industry/Entity Type

Cleaning Service

Number of Pages Required

1 page

Font styles to use
Other font styles liked:
• Proxima Nova

Colors
0355a3
add136

Requirements
Must have
• Most of this is covered in the project description.
• Would like to have our logo split up so that the art of the maids remains the same but the "Tidy Fleet Crew" text is to the right of the art. Looking for it to be a horizontal logo.
• Must use Proxima Nova font.
• Must use our branded images and videos. Feel free to create stills from the video.
Nice to have
• Nice to have, but not expected, is the b-roll edited to work with your design. We would like to see the designers vision of how the video would look with the website.
• Would be nice to have our logo given an updated look. Made horizontal as mentioned in the project description.
Should not have
• Should not feel busy. Should not use different color scheme than that of Sweep Lancers. Should not have non-branded images of maids.

```html
<!DOCTYPE html>
<html lang="en">
<head>
<meta charset="utf-8">
<title>Tidy Fleet Crew – Home Cleaning</title>
<link href="https://fonts.googleapis.com/css2?family=Montserrat:wght@400;600;700;800&family=Mulish:ital,wght@0,400;0,600;0,700;1,400&display=swap" rel="stylesheet">
<style>
:root{
  --blue:#0355a3;
  --blue-dark:#023f7a;
  --green:#add136;
  --green-dark:#8fb023;
  --ink:#2a2f36;
  --muted:#6b7280;
  --line:#e2e5e9;
  --paper:#ffffff;
  --soft:#f4f6f8;
  --footer:#2d2f33;
  --footer-deep:#222427;
}
*{box-sizing:border-box;margin:0;padding:0}
html,body{width:1200px;height:3764px;overflow:hidden}
body{font-family:"Mulish",sans-serif;color:var(--ink);background:var(--paper);position:relative}
h1,h2,h3,h4,.brand-name,.btn{font-family:"Montserrat",sans-serif}
section,header,footer{position:absolute;left:0;width:1200px}

/* Header */
.site-header{top:0;height:60px;display:flex;align-items:center;padding:0 60px;background:var(--paper)}
.brand{display:flex;align-items:center;gap:10px}
.brand-mark{width:30px;height:30px;border-radius:50%;background:var(--green)}
.brand-name{font-weight:700;font-size:18px;color:var(--blue)}
.main-nav{margin-left:auto;display:flex;gap:34px;align-items:center;font-family:"Montserrat",sans-serif;font-size:11px;font-weight:600;color:var(--ink)}
.btn{display:inline-block;border:none;font-weight:700;font-size:11px;text-transform:uppercase;padding:10px 20px;border-radius:3px;color:#fff;background:var(--green)}
.btn-blue{background:var(--blue)}
.main-nav .btn{margin-left:10px}

/* Steps */
.steps{top:60px;height:40px;display:flex;background:#fff;border-top:1px solid var(--line);border-bottom:1px solid var(--line)}
.step{flex:1;display:flex;align-items:center;gap:10px;padding-left:60px;font-family:"Montserrat",sans-serif;font-weight:700;font-size:15px;color:var(--blue)}
.step-num{width:22px;height:22px;border-radius:50%;border:2px solid currentColor;display:flex;align-items:center;justify-content:center;font-size:11px}
.step.is-active{background:var(--green);color:#fff;clip-path:polygon(0 0,94% 0,100% 50%,94% 100%,0 100%)}

/* Hero */
.hero{top:100px;height:780px;background:linear-gradient(180deg,#eef0f2 0%,#d9dde1 60%,#c8cdd2 100%)}
.hero-copy{position:absolute;left:90px;top:70px;width:560px}
.hero-copy h1{font-size:32px;font-weight:800;color:var(--ink);line-height:1.2}
.hero-copy .tagline{margin-top:8px;font-style:italic;font-size:16px;color:var(--blue)}
.hero-list{list-style:none;margin-top:26px}
.hero-list li{display:flex;gap:12px;align-items:flex-start;font-size:14px;line-height:1.4;margin-bottom:14px}
.hero-list svg{flex:none;margin-top:2px}
.hero-car{position:absolute;left:60px;top:430px;width:680px;height:330px;border-radius:140px 160px 40px 40px;background:linear-gradient(160deg,#c7e16a 0%,var(--green) 45%,#7fa21d 100%)}

.quote-form{position:absolute;right:14px;top:-40px;width:216px;background:#fff;box-shadow:0 6px 24px rgba(0,0,0,.15);padding:16px 14px 20px}
.quote-form h2{font-size:24px;font-weight:700;color:var(--ink);margin-bottom:12px}
.field{height:28px;border:1px solid var(--line);border-radius:2px;font-size:10px;color:var(--muted);display:flex;align-items:center;padding:0 8px;margin-bottom:10px;background:#fff}
.form-label{font-size:10px;font-weight:700;color:var(--ink);margin:6px 0 6px}
.toggle{display:flex;margin-bottom:10px}
.toggle span{flex:1;height:26px;display:flex;align-items:center;justify-content:center;font-size:10px;font-weight:700;border:1px solid var(--line)}
.toggle .on{background:var(--blue);color:#fff;border-color:var(--blue)}
.pair{display:flex;gap:8px}
.pair .field{flex:1}
.form-note{font-size:8px;color:var(--muted);margin:-4px 0 8px}
.check{display:flex;align-items:center;gap:6px;font-size:10px;margin:4px 0 14px}
.check i{width:11px;height:11px;border:1px solid var(--muted);display:block}
.quote-form .btn{display:block;width:100%;text-align:center;padding:11px 0}

/* Section heading */
.sec-title{text-align:center;font-size:30px;font-weight:800;color:var(--ink);text-transform:uppercase;line-height:1.2}
.dots{display:flex;justify-content:center;gap:6px;margin-top:14px}
.dots i{width:6px;height:6px;border-radius:50%;background:var(--green)}

/* Eco */
.eco{top:880px;height:660px;background:#fff;padding-top:70px}
.eco-grid{display:flex;justify-content:center;gap:190px;margin-top:50px}
.eco-item{width:260px;text-align:center}
.eco-icon{width:120px;height:120px;border-radius:50%;border:3px solid var(--blue);margin:0 auto 40px;display:flex;align-items:center;justify-content:center}
.eco-item h3{font-size:17px;font-weight:700;margin-bottom:14px}
.eco-item p{font-size:12px;line-height:1.6;color:var(--muted);margin-bottom:22px}

/* Services */
.services{top:1540px;height:520px;background:var(--soft);padding-top:50px}
.services .sec-title{text-transform:none;font-size:36px}
.subtitle{text-align:center;font-size:12px;color:var(--muted);margin-top:6px}
.service-grid{display:flex;justify-content:center;gap:26px;margin-top:50px}
.service{width:250px}
.service-thumb{height:190px;position:relative;display:flex;align-items:center;justify-content:center}
.service h4{font-size:17px;font-weight:700;margin:14px 0 10px}
.share{display:flex;gap:5px}
.share i{width:16px;height:16px;display:block}

/* Testimonials */
.testimonials{top:2060px;height:740px;background:linear-gradient(100deg,#2a2c30 0%,#3d3f44 55%,#5a5650 100%);padding-top:70px}
.testimonials .sec-title{color:#fff}
.review-grid{display:flex;gap:26px;margin:80px 0 0 100px}
.review{width:270px;background:var(--blue);color:#fff;padding:22px 22px 26px;box-shadow:0 8px 22px rgba(0,0,0,.35)}
.review-head{display:flex;gap:14px;align-items:center;margin-bottom:22px}
.avatar{width:62px;height:62px;border-radius:50%;border:3px solid #fff;background:linear-gradient(135deg,#c9b8a6,#8c7b6a)}
.review-head strong{font-family:"Montserrat",sans-serif;font-size:15px;display:block}
.review-head small{font-size:10px;color:var(--green)}
.review p{font-size:12px;line-height:1.6}
.btn-ghost{background:transparent;border:1px solid #fff;position:absolute;left:388px;top:620px;padding:12px 28px}

/* About */
.about{top:2800px;height:580px;padding-top:60px}
.about .sec-title{text-transform:none;font-size:32px}
.about-photo{position:absolute;left:100px;top:140px;width:440px;height:400px;background:linear-gradient(160deg,#f1f3f4 0%,#d8e6b4 55%,#add136 100%)}
.about-copy{position:absolute;left:620px;top:160px;width:480px}
.about-copy p{font-size:12px;line-height:1.7;color:var(--muted);margin-bottom:18px}
.about-actions{display:flex;gap:20px;margin-top:30px}
.about-actions .btn{padding:13px 26px}

/* Press */
.press{top:3380px;height:160px;background:#f7f7f7;display:flex;justify-content:center;align-items:center;gap:40px}
.press-badge{width:220px;height:80px;background:#fff;border:1px solid var(--line);display:flex;align-items:center;justify-content:center}
.press-badge i{width:140px;height:22px;background:#9aa0a6;border-radius:3px;display:block}

/* Footer */
.site-footer{top:3540px;height:224px;background:var(--footer);color:#d6d8db}
.footer-cols{display:flex;gap:80px;padding:26px 100px 0}
.footer-cols h4{color:#fff;font-size:15px;font-weight:700;margin-bottom:14px}
.contact li{list-style:none;display:flex;gap:10px;font-size:11px;line-height:1.5;margin-bottom:10px}
.enquiry p{font-size:10px;margin-bottom:10px;width:190px}
.enquiry .field{width:190px;height:24px;margin-bottom:8px}
.enquiry .btn{padding:7px 16px}
.cards{display:flex;gap:6px}
.cards i{width:40px;height:26px;border-radius:3px;background:#e8eaed;display:block}
.footer-brand{margin-left:auto;display:flex;align-items:center;gap:10px;align-self:center}
.footer-brand .brand-name{color:#fff}
.copyright{position:absolute;bottom:0;left:0;width:100%;height:28px;background:var(--footer-deep);font-size:10px;color:#9ba0a6;display:flex;align-items:center;justify-content:center}
</style>
</head>
<body>

<header class="site-header">
  <div class="brand"><span class="brand-mark"></span><span class="brand-name">Tidy Fleet Crew</span></div>
  <nav class="main-nav">
    <span>FAQ</span><span>SERVICES &amp; PRICING</span><span>LOGIN</span><span>GIFT CARDS</span>
    <span class="btn">Book Call Now</span>
  </nav>
</header>

<div class="steps" style="position:absolute;top:60px;left:0;width:1200px">
  <div class="step is-active"><span class="step-num">1</span>Cleaning</div>
  <div class="step"><span class="step-num">2</span>Pricing/Availability</div>
  <div class="step"><span class="step-num">3</span>Done!</div>
</div>

<section class="hero" role="img" aria-label="Bright kitchen with the branded cleaning car parked in front">
  <div class="hero-copy">
    <h1>Love that feeling of a fresh, clean home?</h1>
    <p class="tagline">Fighting the war on dirt with eco-friendly weapons.</p>
    <ul class="hero-list">
      <li><svg width="14" height="14" viewBox="0 0 14 14"><path d="M2 7l3 3 7-7" stroke="#add136" stroke-width="2.5" fill="none"/></svg>Your friends and family will love how clean your home looks and smells!</li>
      <li><svg width="14" height="14" viewBox="0 0 14 14"><path d="M2 7l3 3 7-7" stroke="#add136" stroke-width="2.5" fill="none"/></svg>Let us handle the cleaning so you can have more free time.</li>
      <li><svg width="14" height="14" viewBox="0 0 14 14"><path d="M2 7l3 3 7-7" stroke="#add136" stroke-width="2.5" fill="none"/></svg>Tidy Fleet Crew is super flexible and affordable.</li>
      <li><svg width="14" height="14" viewBox="0 0 14 14"><path d="M2 7l3 3 7-7" stroke="#add136" stroke-width="2.5" fill="none"/></svg>Backed by our unique 200% Guarantee. You have nothing to lose.</li>
    </ul>
  </div>
  <div class="hero-car" role="img" aria-label="Branded green and white company car"></div>

  <form class="quote-form">
    <h2>Get a Price</h2>
    <div class="field">Zip Code</div>
    <div class="form-label">Cleaning Style</div>
    <div class="toggle"><span class="on">One Time</span><span>Recurring</span></div>
    <div class="form-label">Tell us about your home</div>
    <div class="pair"><div class="field">2 Bedroom</div><div class="field">1 Bathroom</div></div>
    <p class="form-note">Studio counts as one bedroom</p>
    <div class="form-label">When would you like us to come?</div>
    <div class="field">Pick a date</div>
    <div class="form-label">Any time between</div>
    <div class="pair"><div class="field">08:00 am</div><div class="field">05:00 pm</div></div>
    <div class="check"><i></i>I'm Flexible</div>
    <span class="btn btn-blue">Get a Price</span>
  </form>
</section>

<section class="eco">
  <h2 class="sec-title">Super maid service with eco<br>friendly products</h2>
  <div class="dots"><i></i><i></i><i></i><i></i></div>
  <div class="eco-grid">
    <div class="eco-item">
      <div class="eco-icon"><svg width="56" height="56" viewBox="0 0 56 56"><circle cx="28" cy="22" r="14" fill="none" stroke="#0355a3" stroke-width="3"/><path d="M20 34l-4 18 12-6 12 6-4-18" fill="#add136"/><path d="M22 22l4 4 8-8" stroke="#add136" stroke-width="3" fill="none"/></svg></div>
      <h3>Quality Assurance</h3>
      <p>Fresh and thorough, our crew gives every home careful attention. We don't just say it, we prove it. We want to WOW every client and leave them with a smile.</p>
      <span class="btn">Read More</span>
    </div>
    <div class="eco-item">
      <div class="eco-icon"><svg width="56" height="56" viewBox="0 0 56 56"><rect x="24" y="6" width="8" height="30" fill="#0355a3"/><path d="M14 36h28l4 14H10z" fill="#add136"/></svg></div>
      <h3>Flexible and Affordable</h3>
      <p>Book one time or on a schedule that suits you. Clear prices, no hidden fees. We want to WOW every client and leave them with a smile.</p>
      <span class="btn">Read More</span>
    </div>
    <div class="eco-item">
      <div class="eco-icon"><svg width="56" height="56" viewBox="0 0 56 56"><path d="M8 26h10v22H8z" fill="#0355a3"/><path d="M20 26l10-18c4 0 6 3 5 7l-2 8h13c3 0 5 3 4 6l-4 16c-1 2-3 3-5 3H20z" fill="#add136"/></svg></div>
      <h3>Guarantee</h3>
      <p>If anything is missed, tell us and we will return to fix it at no cost. We want to WOW every client and leave them with a smile.</p>
      <span class="btn">Read More</span>
    </div>
  </div>
</section>

<section class="services">
  <h2 class="sec-title">Our Services</h2>
  <p class="subtitle">Let Tidy Fleet Crew Make Your Life Easier</p>
  <div class="service-grid">
    <div class="service">
      <div class="service-thumb" role="img" aria-label="Video still of a maid cleaning a bathroom" style="background:linear-gradient(135deg,#dfe5ea,#9fb2c2)"><svg width="44" height="44" viewBox="0 0 44 44"><circle cx="22" cy="22" r="20" fill="rgba(0,0,0,.45)"/><path d="M17 13l13 9-13 9z" fill="#fff"/></svg></div>
      <h4>Wet Areas</h4>
      <div class="share"><i style="background:#0355a3"></i><i style="background:#5aa9e6"></i><i style="background:#c0392b"></i><i style="background:#add136"></i></div>
    </div>
    <div class="service">
      <div class="service-thumb" role="img" aria-label="Video still of a maid wiping kitchen counters" style="background:linear-gradient(135deg,#e9e4dc,#b9ad9a)"><svg width="44" height="44" viewBox="0 0 44 44"><circle cx="22" cy="22" r="20" fill="rgba(0,0,0,.45)"/><path d="M17 13l13 9-13 9z" fill="#fff"/></svg></div>
      <h4>Kitchen</h4>
      <div class="share"><i style="background:#0355a3"></i><i style="background:#5aa9e6"></i><i style="background:#c0392b"></i><i style="background:#add136"></i></div>
    </div>
    <div class="service">
      <div class="service-thumb" role="img" aria-label="Video still of a maid dusting an interior" style="background:linear-gradient(135deg,#e6e9ee,#a8b4c6)"><svg width="44" height="44" viewBox="0 0 44 44"><circle cx="22" cy="22" r="20" fill="rgba(0,0,0,.45)"/><path d="M17 13l13 9-13 9z" fill="#fff"/></svg></div>
      <h4>Interiors Service</h4>
      <div class="share"><i style="background:#0355a3"></i><i style="background:#5aa9e6"></i><i style="background:#c0392b"></i><i style="background:#add136"></i></div>
    </div>
    <div class="service">
      <div class="service-thumb" role="img" aria-label="Video still of a maid tidying a living room" style="background:linear-gradient(135deg,#efe6da,#c2a88a)"><svg width="44" height="44" viewBox="0 0 44 44"><circle cx="22" cy="22" r="20" fill="rgba(0,0,0,.45)"/><path d="M17 13l13 9-13 9z" fill="#fff"/></svg></div>
      <h4>Living Areas</h4>
      <div class="share"><i style="background:#0355a3"></i><i style="background:#5aa9e6"></i><i style="background:#c0392b"></i><i style="background:#add136"></i></div>
    </div>
  </div>
</section>

<section class="testimonials" role="img" aria-label="Dim kitchen scene with a maid cleaning a table">
  <h2 class="sec-title">What our clients say</h2>
  <div class="dots"><i></i><i></i><i></i><i></i></div>
  <div class="review-grid">
    <div class="review">
      <div class="review-head"><span class="avatar" role="img" aria-label="Client portrait"></span><div><strong>Marisol</strong><small>Weekly Cleaning</small></div></div>
      <p>When I booked, my home hadn't been cleaned in weeks. The crew arrived on time, worked hard and left every room spotless. I came home to a fresh house and a calm evening. Thank you!</p>
    </div>
    <div class="review">
      <div class="review-head"><span class="avatar" role="img" aria-label="Client portrait"></span><div><strong>Marisol</strong><small>Weekly Cleaning</small></div></div>
      <p>When I booked, my home hadn't been cleaned in weeks. The crew arrived on time, worked hard and left every room spotless. I came home to a fresh house and a calm evening. Thank you!</p>
    </div>
    <div class="review">
      <div class="review-head"><span class="avatar" role="img" aria-label="Client portrait"></span><div><strong>Marisol</strong><small>Weekly Cleaning</small></div></div>
      <p>When I booked, my home hadn't been cleaned in weeks. The crew arrived on time, worked hard and left every room spotless. I came home to a fresh house and a calm evening. Thank you!</p>
    </div>
  </div>
  <span class="btn btn-ghost">View More Reviews</span>
</section>

<section class="about">
  <h2 class="sec-title">Make Life Better with Tidy Fleet Crew</h2>
  <div class="dots"><i></i><i></i><i></i><i></i></div>
  <div class="about-photo" role="img" aria-label="Two smiling maids in green company uniforms"></div>
  <div class="about-copy">
    <p>First and foremost, Tidy Fleet Crew provides world class customer service. We don't just say that, we prove it every visit. We want to WOW every single customer and leave them with a smile. We want to improve your life so that you can focus on what matters most, and we are always ready to help.</p>
    <p>Each visit is handled by trained, background-checked cleaners who use eco-friendly products that are safe for kids and pets. Your home is left fresh, healthy and ready to enjoy, so you can spend your time on family, work and rest.</p>
    <div class="about-actions"><span class="btn">Get Instant Price</span><span class="btn btn-blue">About Us</span></div>
  </div>
</section>

<section class="press" aria-label="Featured in">
  <div class="press-badge"><i></i></div>
  <div class="press-badge"><i></i></div>
  <div class="press-badge"><i></i></div>
  <div class="press-badge"><i></i></div>
</section>

<footer class="site-footer">
  <div class="footer-cols">
    <div class="contact">
      <h4>Contact us</h4>
      <ul>
        <li><svg width="12" height="14" viewBox="0 0 12 14"><path d="M6 0a5 5 0 015 5c0 4-5 9-5 9S1 9 1 5a5 5 0 015-5z" fill="#add136"/><circle cx="6" cy="5" r="2" fill="#2d2f33"/></svg>1420 Maple Crest Drive<br>Orlando, FL 32803</li>
        <li><svg width="12" height="12" viewBox="0 0 12 12"><rect x="0" y="2" width="12" height="8" fill="#add136"/><path d="M0 2l6 5 6-5" stroke="#2d2f33" fill="none"/></svg>hello@tidyfleetcrew.example</li>
        <li><svg width="12" height="12" viewBox="0 0 12 12"><path d="M2 0l3 3-1.5 2a7 7 0 003.5 3.5L9 7l3 3-2 2C5 12 0 7 0 2z" fill="#add136"/></svg>(407) 555-0142</li>
      </ul>
    </div>
    <div class="enquiry">
      <h4>Enquiry us</h4>
      <p>Have a question? Send us a note and our team will reply fast.</p>
      <div class="field">Name</div>
      <div class="field">Email</div>
      <span class="btn">Submit</span>
    </div>
    <div>
      <h4>We Accept</h4>
      <div class="cards"><i></i><i></i></div>
      <div class="cards" style="margin-top:6px"><i></i><i></i></div>
    </div>
    <div class="footer-brand"><span class="brand-mark"></span><span class="brand-name">Tidy Fleet Crew</span></div>
  </div>
  <div class="copyright">Copyright © 2024 Tidy Fleet Crew. All rights reserved.</div>
</footer>

</body>
</html>
```